Blow Dry Bar Business Cards

These cards must be eye catching and modern.
You must be willing to work fast and make changes.

Winner will be offered other projects

Files 1 THIS IS THE STYLE CARDS I AM INTRESTED IN!!!
Please be creative, I am paying for my own eye catching design. I need files to be nexa press ready.

COLORS THAT ARE PAINTED INSIDE MY SHOP:
- - - http://www.quorvelpaint.example/en/explore-colors/painter/color-selector.html?colors=4007-3C

- - - http://www.brandivex.example/color/paint-colors/hidden-corridor-d58-2

I want the business cards sleek and modern if you use the logo please correct imperfections. I added the part that says Blow Dry Bar (see website).
Do not be afraid to separate the blow dryer from the name to make the cards look like the file with the pink elephant.

SHOULD INCLUDE
*Blow Dryer (we are a blow dry bar not a salon we do not cut or color so do not include sheers of any kind)
*BUSINESS NAME: Simply Swept Upward - Blow Dry Bar (PLEASE SEE MY WEBSITE)
* Website: SIMPLYSWEPTUPWARD.EXAMPLE
*Phone number (555) 014-2763
Updates

Nexa press said it can be submitted in JPG

http://www.brandivex.example/color/paint-colors/hidden-corridor-d58-2 http://www.quorvelpaint.example/en/explore-colors/painter/color-selector.html?colors=4007-3C ^^^^ These links will take you to the color paint that is painted inside my shop.

Target Market(s)

AGES 18 - 55 WOMEN
HIGH END MARKET

Industry/Entity Type

Salon

Requirements
Must have
• SEE COLOR EXAMPLE FILE
BLOW DRYER
UNIQUE
I LIKE THE CARD WITH THE PINK ELEPHANT THE BEST
Nice to have
• BE AS CREATIVE AND MODERN AS POSSIBLE DO NOT COPY ANY OF THE CARDS BELOW.
Should not have
• SCISSORS
PINK

```html
<!DOCTYPE html>
<html lang="en">
<head>
<meta charset="utf-8">
<title>Swept Upward – Business Cards</title>
<link rel="stylesheet" href="https://fonts.googleapis.com/css2?family=Arvo:wght@400&family=Roboto:wght@400&display=swap">
<style>
  :root {
    --backdrop: #e9e6e2;
    --card-black: #0d0d0d;
    --shop-purple: #5e3f7f;
    --brand-yellow: #f5c51e;
    --panel-yellow-light: #f8d040;
    --panel-yellow-deep: #eeb915;
  }
  html, body {
    margin: 0;
    width: 1200px;
    height: 914px;
    overflow: hidden;
    background: var(--backdrop);
  }
  .sheet {
    position: relative;
    width: 1200px;
    height: 914px;
  }
  .card {
    position: absolute;
    left: 250px;
    width: 700px;
    height: 400px;
    box-shadow: 0 6px 18px rgba(0,0,0,0.18);
  }
  .card--logo { top: 40px; }
  .card--contact { top: 474px; }
  .card svg { display: block; }
  .brand-name {
    font-family: "Arvo", serif;
    font-weight: 400;
    fill: var(--brand-yellow);
  }
  .contact-line {
    font-family: "Roboto", sans-serif;
    font-size: 14px;
    letter-spacing: 0.2px;
    fill: var(--brand-yellow);
  }
  .contact-icon { fill: var(--brand-yellow); }
</style>
</head>
<body>
<main class="sheet">

  <section class="card card--logo" aria-label="Business card, logo side">
    <svg width="700" height="400" viewBox="0 0 700 400">
      <rect class="card-base" width="700" height="400" fill="var(--card-black)"/>
      <rect class="accent-stripe" x="0" y="272" width="700" height="8" fill="var(--brand-yellow)"/>
      <rect class="purple-band" x="0" y="280" width="700" height="120" fill="var(--shop-purple)"/>
      <text class="brand-name" x="350" y="165" font-size="70" text-anchor="middle">Swept Upward</text>
    </svg>
  </section>

  <section class="card card--contact" aria-label="Business card, contact side">
    <svg width="700" height="400" viewBox="0 0 700 400">
      <rect class="card-base" width="700" height="400" fill="var(--card-black)"/>
      <polygon class="contact-panel" points="0,150 360,150 415,400 0,400" fill="var(--shop-purple)"/>
      <defs>
        <linearGradient id="dryerPanelTone" x1="0" y1="0" x2="1" y2="1">
          <stop offset="0" stop-color="var(--panel-yellow-light)"/>
          <stop offset="1" stop-color="var(--panel-yellow-deep)"/>
        </linearGradient>
      </defs>
      <polygon class="product-panel" points="383,195 700,195 700,400 428,400"
               fill="url(#dryerPanelTone)" role="img"
               aria-label="Photo of four colourful professional blow dryers in purple, violet, red and green"/>

      <text class="brand-name" x="40" y="105" font-size="66">Swept Upward</text>

      <!-- phone -->
      <path class="contact-icon" d="M30 184c1-2 3-3 4-2l3 4c1 1 0 2-1 3l-1 1c1 3 3 5 6 6l1-1c1-1 2-2 3-1l4 3c1 1 0 3-2 4-6 2-18-10-17-17z"/>
      <text class="contact-line" x="56" y="197">(555) 014-2763</text>

      <!-- globe -->
      <circle class="contact-icon" cx="38" cy="220" r="8"/>
      <path d="M30 220h16M38 212c-4 5-4 11 0 16M38 212c4 5 4 11 0 16" stroke="var(--shop-purple)" stroke-width="1.4" fill="none"/>
      <text class="contact-line" x="56" y="225">SIMPLYSWEPTUPWARD.EXAMPLE</text>

      <!-- envelope -->
      <rect class="contact-icon" x="30" y="243" width="16" height="11" rx="1"/>
      <path d="M30 244l8 6 8-6" stroke="var(--shop-purple)" stroke-width="1.4" fill="none"/>
      <text class="contact-line" x="56" y="253">INFO@SIMPLYSWEPTUPWARD.EXAMPLE</text>

      <!-- pin -->
      <path class="contact-icon" d="M38 270a7 7 0 0 1 7 7c0 5-7 12-7 12s-7-7-7-12a7 7 0 0 1 7-7z"/>
      <circle cx="38" cy="277" r="2.6" fill="var(--shop-purple)"/>
      <text class="contact-line" x="56" y="282">482 HERON BAY DRIVE SUITE 9</text>
      <text class="contact-line" x="56" y="302">MAPLE HARBOR, TEXAS 75010</text>
    </svg>
  </section>

</main>
</body>
</html>
```